Copper Lantern

Need a business card for our restaurant. Restaurant and Bar in the mountains of North Idaho. Rustic looking card

rustic design, wood and metal looking, primarily neutral colors

• Name, address, phone number, website, email address

```html
<!DOCTYPE html>
<html lang="en">
<head>
<meta charset="utf-8">
<title>Copper Lantern – Business Card</title>
<link href="https://fonts.googleapis.com/css2?family=Montserrat:wght@400;500;600&display=swap" rel="stylesheet">
<style>
  :root {
    --page-bg: #d8d1c6;
    --card-dark: #1d1a17;
    --card-dark-edge: #3a342e;
    --card-light: #e7dccb;
    --text-light: #e9dfcf;
    --text-muted: #cbbfae;
    --ink: #1c1916;
  }
  html, body {
    margin: 0;
    padding: 0;
    width: 1200px;
    height: 1047px;
    overflow: hidden;
    background: var(--page-bg);
  }
  .card {
    position: absolute;
    left: 100px;
    top: 252px;
    width: 1000px;
    height: 544px;
    border-radius: 22px;
    overflow: hidden;
    box-shadow: 0 18px 40px rgba(0,0,0,0.18);
    font-family: "Montserrat", sans-serif;
  }
  .card-shapes {
    position: absolute;
    inset: 0;
  }
  .holder {
    position: absolute;
    left: 40px;
    top: 52px;
    color: var(--text-light);
  }
  .holder-name {
    margin: 0;
    font-size: 39px;
    font-weight: 600;
    letter-spacing: 0.5px;
  }
  .holder-title {
    margin: 8px 0 0;
    font-size: 24px;
    font-weight: 400;
    color: var(--text-muted);
  }
  .address {
    position: absolute;
    left: 40px;
    top: 212px;
    margin: 0;
    font-size: 25px;
    line-height: 38px;
    color: var(--text-muted);
    font-style: normal;
  }
  .contacts {
    position: absolute;
    left: 40px;
    top: 370px;
    margin: 0;
    padding: 0;
    list-style: none;
    font-size: 25px;
    color: var(--text-muted);
  }
  .contacts li {
    display: flex;
    align-items: center;
    height: 38px;
  }
  .contacts svg {
    width: 18px;
    height: 18px;
    margin-right: 14px;
    fill: var(--text-muted);
  }
  .brand {
    position: absolute;
    left: 415px;
    top: 0;
    width: 604px;
    height: 544px;
    display: flex;
    align-items: center;
    justify-content: center;
    margin: 0;
    font-size: 46px;
    font-weight: 500;
    letter-spacing: 3px;
    text-transform: uppercase;
    color: var(--ink);
    text-align: center;
    line-height: 1.2;
  }
</style>
</head>
<body>
  <div class="card">
    <svg class="card-shapes" width="1000" height="544" viewBox="0 0 1000 544">
      <defs>
        <linearGradient id="dark-panel" x1="0" y1="0" x2="1" y2="0">
          <stop offset="0" stop-color="var(--card-dark-edge)"/>
          <stop offset="0.3" stop-color="var(--card-dark)"/>
          <stop offset="1" stop-color="var(--card-dark)"/>
        </linearGradient>
      </defs>
      <rect class="panel-dark" width="1000" height="544" fill="url(#dark-panel)"/>
      <rect class="panel-light" x="717" y="0" width="283" height="544" fill="var(--card-light)"/>
      <circle class="panel-light-circle" cx="717" cy="250" r="302" fill="var(--card-light)"/>
    </svg>

    <div class="holder">
      <h1 class="holder-name">Owen Hartley</h1>
      <p class="holder-title">Managing Director</p>
    </div>

    <address class="address">Your address, City<br>State, Zip 1234</address>

    <ul class="contacts">
      <li>
        <svg viewBox="0 0 24 24" aria-hidden="true"><path d="M6.6 10.8a15.1 15.1 0 0 0 6.6 6.6l2.2-2.2a1 1 0 0 1 1-.25 11.4 11.4 0 0 0 3.6.57 1 1 0 0 1 1 1V20a1 1 0 0 1-1 1A17 17 0 0 1 3 4a1 1 0 0 1 1-1h3.5a1 1 0 0 1 1 1c0 1.25.2 2.45.57 3.57a1 1 0 0 1-.25 1z"/></svg>
        123 456 789
      </li>
      <li>
        <svg viewBox="0 0 24 24" aria-hidden="true"><path d="M2 5h20v14H2z M3.5 6.5 12 13l8.5-6.5" stroke="var(--card-dark)" stroke-width="1.6"/></svg>
        info@yourgmail.com
      </li>
      <li>
        <svg viewBox="0 0 24 24" aria-hidden="true"><circle cx="12" cy="12" r="10"/><path d="M2 12h20M12 2c3 3 3 17 0 20M12 2c-3 3-3 17 0 20" stroke="var(--card-dark)" stroke-width="1.4" fill="none"/></svg>
        www.yourwebsite.com
      </li>
    </ul>

    <p class="brand">Copper<br>Lantern</p>
  </div>
</body>
</html>
```